Government Contracting business needs a website design.

Pellworth & Quine, LLC is a minority owned Service Disabled Veteran Owned Small Business (SDVOSB) that provides Strategic Planning, Public Health Emergency Response, and Data Management Solutions for Federal Civilian and Defense Agencies. We have over 20 years of experience helping health and defense agencies develop concept of operations, deploy assets and personnel in Hot Zones around the world, and deliver goods and services all of the globe.

We are a leader in the field of Data Management. We help our customers develop cloud migration and disaster recovery strategies. We are experts with database management, data replication, queries, consolidation, and records management.

We are looking for a very nice and simple website designs that states clearly what we do as a company and that is easy for our customers to follow. We would like to have some moving pictures that are base on our expertise. We want the website to be easy to use and have the scroll down features that keeps things all on the same page when clicking on the menu. I attached a document with what we need on the website. I will also attach our logo. We want it to look simple clean and very professional.

Target Market(s)

Government Contracting, Management Consulting, Health

Industry/Entity Type

Government

Coding

Coded - Design and coding required

Number of Pages Required

1 page

Font styles to use
Serif

Requirements
Must have
• Very nice picture slides that speaks to our capabilities in Disaster Response, Strategic Planning, and Database Management. Slick look and design. Make sure SDVOSB Logo is right at the beginning of website as our customers is looking for that certification. Very nice colors that blend well with our logo.
Nice to have
• Very nice and slick colors that blends well with logo.
Should not have
• Basic website design that are weary on the eye. No bright colors, just simple colors that looks good with logo.

```html
<!DOCTYPE html>
<html lang="en">
<head>
<meta charset="utf-8">
<title>Pellworth &amp; Quine, LLC</title>
<link href="https://fonts.googleapis.com/css2?family=Open+Sans:wght@400;600;700&family=Libre+Baskerville:wght@400;700&display=swap" rel="stylesheet">
<style>
:root{
  --navy:#1d3447;
  --navy-deep:#152735;
  --slate:#2e4a5e;
  --band:#30495a;
  --ink:#2a2f35;
  --muted:#6b737b;
  --line:#d9dde1;
  --soft:#f1f2f4;
  --white:#ffffff;
}
*{box-sizing:border-box;margin:0;padding:0}
html,body{width:1200px;height:3040px;overflow:hidden}
body{font-family:"Open Sans",Arial,sans-serif;color:var(--ink);background:var(--white);position:relative}
.serif{font-family:"Libre Baskerville",Georgia,serif}

.site-header{position:absolute;top:0;left:0;width:1200px;height:100px;background:var(--white)}
.brand{position:absolute;left:40px;top:26px;display:flex;align-items:center;gap:14px}
.brand-mark{width:40px;height:40px;background:var(--navy)}
.brand-name{font-family:"Libre Baskerville",Georgia,serif;font-size:26px;color:var(--navy);font-weight:400}
.call{position:absolute;right:60px;top:8px;display:flex;align-items:center;gap:8px;color:var(--navy)}
.call small{display:block;font-size:10px;color:var(--muted)}
.call strong{font-size:15px}
.main-nav{position:absolute;right:0;top:58px;width:680px;height:38px;background:var(--navy-deep);display:flex;align-items:center;padding-left:20px;gap:4px}
.main-nav a{color:var(--white);font-size:11px;font-weight:600;letter-spacing:.5px;text-decoration:none;padding:8px 14px}
.main-nav a.active{background:var(--white);color:var(--navy)}
.search{margin-left:auto;margin-right:24px;width:130px;height:24px;border:1px solid #5a6b78;color:#a9b3bb;font-size:10px;padding:5px 8px}

.hero{position:absolute;top:100px;left:0;width:1200px;height:420px;background:linear-gradient(120deg,#dfe3e6 0%,#c9cfd4 45%,#8d9aa4 100%)}
.hero-caption{position:absolute;left:140px;top:190px;width:270px;padding:18px;background:rgba(29,52,71,.55);color:var(--white)}
.hero-caption h2{font-size:20px;font-weight:700;letter-spacing:.5px;margin-bottom:10px}
.hero-caption p{font-size:11px;line-height:1.5;margin-bottom:14px}
.btn{display:inline-block;background:var(--navy);color:var(--white);font-size:10px;font-weight:700;letter-spacing:.5px;padding:9px 16px}
.hero-arrow{position:absolute;top:345px;width:24px;height:30px;background:rgba(21,39,53,.75);display:flex;align-items:center;justify-content:center}
.badge{position:absolute;left:570px;top:480px;width:80px;height:80px;border-radius:50%;background:var(--white);border:5px solid #2b4a7a}

.section-title{text-align:center;font-size:22px;font-weight:700;color:var(--navy)}
.title-mark{display:block;margin:10px auto 0;width:22px;height:10px;background:var(--slate)}

.capabilities{position:absolute;top:700px;left:0;width:1200px}
.cap-row{display:flex;justify-content:space-between;width:760px;margin:70px auto 0}
.cap{width:220px}
.cap svg{display:block;margin:0 auto 24px 0}
.cap h3{font-size:14px;font-weight:700;margin-bottom:12px;color:var(--ink)}
.cap li{list-style:none;font-size:10.5px;color:var(--muted);line-height:1.7}

.welcome{position:absolute;top:1175px;left:0;width:1200px;height:370px;background:var(--soft)}
.welcome-text{position:absolute;left:130px;top:50px;width:340px}
.welcome-text .lead{font-size:18px;color:var(--ink)}
.welcome-text h2{font-size:26px;color:var(--navy);margin:4px 0 24px}
.welcome-text p{font-size:11px;line-height:1.65;color:var(--muted);margin-bottom:26px}
.welcome-photo{position:absolute;left:620px;top:0;width:580px;height:370px;background:linear-gradient(135deg,#c3d3e2 0%,#6f8aa3 50%,#2f455b 100%)}

.jobs{position:absolute;top:1665px;left:0;width:1200px}
.job-row{display:flex;justify-content:center;gap:6px;margin-top:60px}
.job{width:160px;height:160px;border:1px solid var(--line);background:var(--white);display:flex;flex-direction:column;align-items:center;justify-content:center;gap:18px}
.job span{font-size:12px;font-weight:700;color:var(--ink);text-align:center;line-height:1.3}

.join{position:absolute;top:2075px;left:0;width:1200px;height:425px;background:linear-gradient(90deg,#121418 0%,#2a1d14 45%,#8a4a1e 75%,#3a2418 100%)}
.join-text{position:absolute;left:140px;top:80px;width:300px;color:var(--white)}
.join-text h2{font-size:22px;margin-bottom:18px}
.join-text p{font-size:11px;line-height:1.6;color:#d6d8db;margin-bottom:24px}
.btn-dark{background:var(--slate)}

.stats{position:absolute;top:2500px;left:0;width:1200px;height:140px;background:var(--band);display:flex;justify-content:center}
.stat{width:230px;border-left:1px solid #4c6576;padding:26px 22px;font-size:10.5px;line-height:1.6;color:#d4dbe0}
.stat:last-child{border-right:1px solid #4c6576}

.site-footer{position:absolute;top:2640px;left:0;width:1200px;height:340px;background:var(--white)}
.foot-brand{position:absolute;left:130px;top:100px}
.foot-col{position:absolute;top:90px}
.foot-col h4{font-size:11px;font-weight:700;color:var(--ink);margin-bottom:16px;letter-spacing:.5px}
.foot-col li{list-style:none;font-size:10.5px;color:var(--muted);line-height:1.8;display:flex;align-items:center;gap:8px}
.social li{margin-bottom:12px}
.dot{width:20px;height:20px;border-radius:50%;background:var(--slate);display:inline-block}
.copyright{position:absolute;top:2980px;left:0;width:1200px;height:60px;border-top:1px solid var(--line);text-align:center;font-size:10px;color:var(--muted);padding-top:20px}
</style>
</head>
<body>

<header class="site-header">
  <div class="brand"><span class="brand-mark"></span><span class="brand-name">Pellworth &amp; Quine</span></div>
  <div class="call">
    <svg width="20" height="20" viewBox="0 0 24 24"><path fill="#1d3447" d="M6.6 10.8c1.4 2.8 3.8 5.1 6.6 6.6l2.2-2.2c.3-.3.7-.4 1-.2 1.1.4 2.3.6 3.6.6.6 0 1 .4 1 1V20c0 .6-.4 1-1 1C10.6 21 3 13.4 3 4c0-.6.4-1 1-1h3.5c.6 0 1 .4 1 1 0 1.3.2 2.5.6 3.6.1.3 0 .7-.2 1z"/></svg>
    <div><small>Call us</small><strong>555.014.2290</strong></div>
  </div>
  <nav class="main-nav">
    <a class="active">HOME</a><a>ABOUT US</a><a>SERVICES</a><a>JOB OPENINGS</a><a>CONTACT US</a>
    <div class="search">Search</div>
  </nav>
</header>

<section class="hero">
  <div role="img" aria-label="Photo of a person at a laptop reviewing financial charts on a desk" style="position:absolute;inset:0"></div>
  <div class="hero-caption">
    <h2>STRATEGIC PLANNING</h2>
    <p>Pellworth &amp; Quine, LLC is a minority owned Service Disabled Veteran Owned Small Business that provides expert Strategic Planning.</p>
    <span class="btn">READ MORE</span>
  </div>
  <div class="hero-arrow" style="left:0"><svg width="10" height="12" viewBox="0 0 10 12"><path d="M8 1 2 6l6 5" stroke="#fff" stroke-width="2" fill="none"/></svg></div>
  <div class="hero-arrow" style="right:0"><svg width="10" height="12" viewBox="0 0 10 12"><path d="M2 1l6 5-6 5" stroke="#fff" stroke-width="2" fill="none"/></svg></div>
</section>
<div class="badge" aria-label="Certification badge"></div>

<section class="capabilities">
  <h2 class="section-title">Core Capabilities</h2><span class="title-mark"></span>
  <div class="cap-row">
    <div class="cap">
      <svg width="40" height="40" viewBox="0 0 40 40"><rect x="6" y="6" width="28" height="20" fill="none" stroke="#2a2f35" stroke-width="2.5"/><path d="M20 26v8M14 36l6-6 6 6M11 20l6-6 5 4 7-7" stroke="#2a2f35" stroke-width="2.5" fill="none"/></svg>
      <h3>Strategic Planning</h3>
      <ul><li>Organizational Needs Assessment</li><li>Strategy Development</li><li>Marketing Outreach</li><li>Cost Benefit and Alternative Analysis</li><li>Leadership Training</li></ul>
    </div>
    <div class="cap">
      <svg width="40" height="40" viewBox="0 0 40 40"><path d="M15 4h10v11h11v10H25v11H15V25H4V15h11z" fill="#2a2f35"/></svg>
      <h3>Public Health Emergency Response</h3>
      <ul><li>Crisis Management</li><li>Disaster Relief Planning</li><li>Asset and Personnel Deployment</li><li>Financial Impact Analysis</li></ul>
    </div>
    <div class="cap">
      <svg width="40" height="40" viewBox="0 0 40 40"><circle cx="20" cy="20" r="13" fill="none" stroke="#2a2f35" stroke-width="5" stroke-dasharray="6 4"/><circle cx="20" cy="20" r="6" fill="#2a2f35"/></svg>
      <h3>Data Management Services</h3>
      <ul><li>Cloud Migration</li><li>Disaster Recovery Strategy</li><li>Database Replication</li><li>Records Management</li></ul>
    </div>
  </div>
</section>

<section class="welcome">
  <div class="welcome-text">
    <div class="lead">Welcome to</div>
    <h2 class="serif">Pellworth &amp; Quine</h2>
    <p>Pellworth &amp; Quine, LLC is a minority owned Service Disabled Veteran Owned Small Business (SDVOSB) that provides Strategic Planning, Public Health Emergency Response, and Data Management Solutions for Federal Civilian and Defense Agencies. We have over 20 years of experience helping health and defense agencies develop concepts of operations, deploy assets and personnel in Hot Zones around the world, and deliver goods and services all over the globe.</p>
    <span class="btn">READ MORE</span>
  </div>
  <div class="welcome-photo" role="img" aria-label="Photo of a team meeting around laptops in a bright office"></div>
</section>

<section class="jobs">
  <h2 class="section-title">Job Openings</h2><span class="title-mark"></span>
  <div class="job-row">
    <div class="job"><svg width="36" height="32" viewBox="0 0 36 32"><rect x="3" y="3" width="30" height="20" fill="none" stroke="#1d3447" stroke-width="2.5"/><path d="M18 23v7M12 30h12" stroke="#1d3447" stroke-width="2.5"/></svg><span>Strategic Planners</span></div>
    <div class="job"><svg width="36" height="32" viewBox="0 0 36 32"><circle cx="18" cy="8" r="5" fill="#1d3447"/><circle cx="6" cy="14" r="4" fill="#1d3447"/><circle cx="30" cy="14" r="4" fill="#1d3447"/><path d="M10 30c0-7 4-10 8-10s8 3 8 10z" fill="#1d3447"/></svg><span>Program Managers</span></div>
    <div class="job"><svg width="36" height="32" viewBox="0 0 36 32"><rect x="4" y="20" width="6" height="10" fill="#1d3447"/><rect x="14" y="14" width="6" height="16" fill="#1d3447"/><rect x="24" y="8" width="6" height="22" fill="#1d3447"/><path d="M3 14 14 6l8 4 11-8" stroke="#1d3447" stroke-width="2" fill="none"/></svg><span>Financial Analysts</span></div>
    <div class="job"><svg width="36" height="32" viewBox="0 0 36 32"><path d="M18 28 5 15a7 7 0 0 1 13-8 7 7 0 0 1 13 8z" fill="#1d3447"/><path d="M14 14h8M18 10v8" stroke="#fff" stroke-width="2.5"/></svg><span>Health Care<br>Professionals</span></div>
    <div class="job"><svg width="36" height="32" viewBox="0 0 36 32"><ellipse cx="18" cy="6" rx="11" ry="4" fill="#1d3447"/><path d="M7 9v6c0 2 5 4 11 4s11-2 11-4V9c0 2-5 4-11 4S7 11 7 9zm0 9v6c0 2 5 4 11 4s11-2 11-4v-6c0 2-5 4-11 4S7 20 7 18z" fill="#1d3447"/></svg><span>Database<br>Administrators</span></div>
  </div>
</section>

<section class="join">
  <div role="img" aria-label="Photo of emergency responders silhouetted against a fire" style="position:absolute;inset:0"></div>
  <div class="join-text">
    <h2>Join Us</h2>
    <p>Pellworth &amp; Quine strives to provide an outstanding work environment for our employees. We invest in our people and deliver strategic consulting and emergency solutions to our clients. Our team members enjoy competitive benefits, steady career growth, and meaningful work that serves the public.</p>
    <span class="btn btn-dark">JOIN NOW</span>
  </div>
</section>

<section class="stats">
  <div class="stat">Over 20 years of experience helping health and defense agencies plan for the future.</div>
  <div class="stat">Over 20 years of experience deploying assets and personnel to Hot Zones around the world.</div>
  <div class="stat">Over 15 years of experience with database management and replication.</div>
  <div class="stat">Highly educated consultants with over fifty years of combined service.</div>
</section>

<footer class="site-footer">
  <div class="foot-brand brand" style="position:absolute;left:130px;top:100px"><span class="brand-mark"></span><span class="brand-name">Pellworth &amp; Quine</span></div>
  <div class="foot-col" style="left:500px">
    <h4>CONTACT US</h4>
    <ul><li>2840 Harlow Street Suite 6</li><li>Alderton, VA 22140</li><li>555.014.2290</li><li>info@pellworthquine.com</li></ul>
  </div>
  <div class="foot-col" style="left:760px">
    <h4>MENU</h4>
    <ul><li>Home</li><li>About Us</li><li>Services</li><li>Job Openings</li><li>Contact Us</li></ul>
  </div>
  <div class="foot-col social" style="left:940px">
    <h4>CONNECT WITH US</h4>
    <ul><li><span class="dot"></span>Socialbook</li><li><span class="dot"></span>Chirper</li><li><span class="dot"></span>ProLink</li></ul>
  </div>
</footer>
<div class="copyright">Copyright © 2016 Pellworth &amp; Quine. All Rights Reserved</div>

</body>
</html>
```